brovlanepass.net

Develop a website for brolanepass.net will be a site to sell tickets for concerts, shows, shows, theaters and others. I need a web design easy view, very easy to use and accumulate events by date. The aim is to develop the site was connected to a complex system that is already developed. (Important this page to a robust system was connected via links the idea is to develop only the front view)
Updates

Reason: I need more designs yet we have not made the decision

Target Market(s)

millennials, adults, who want to enjoy concerts and shows

Industry/Entity Type

Event

Number of Pages Required

5+ page

Colors
1b1b1b
aaaaaa
ffffff

Requirements
Must have
• Easy Vista, accumulation of upcoming events, past events. The tabs should have are: 1 Start: In this part of upcoming events occur. You could put a banner on the top and down the events by date. 2. How to order: page with instructions on how to purchase tickets 3. About Us: The company history 4. Contact: Phones and template for contact by mail 5. Our policies: shopping 6. Notice Privacy: Privacy Notice Copoy 7. Centers Sale: physical places where they can purchase tickets Promoters 8. access: Link to a template
Nice to have
• as you can see p www.quimbarostage.net or farunda.net or farunda.org or gallowmerk.net (important this page to a robust system was connected via links the idea is to develop only the front view)
Should not have
• Many things Tangled

```html
<!DOCTYPE html>
<html lang="en">
<head>
<meta charset="utf-8">
<title>Brovlane Pass</title>
<link href="https://fonts.googleapis.com/css2?family=Montserrat:wght@500;700&family=Open+Sans:wght@400;600&display=swap" rel="stylesheet">
<style>
  :root {
    --page-bg: #1c0a14;
    --page-bg-deep: #12060d;
    --header-bg: #1f0c16;
    --nav-bg: #141214;
    --footer-bg: #111010;
    --accent: #e5474c;
    --accent-dark: #b9343a;
    --text: #ffffff;
    --muted: #aaaaaa;
    --card-strip: rgba(20, 14, 18, 0.82);
    --line: #3a3a3a;
  }
  * { box-sizing: border-box; margin: 0; padding: 0; }
  html, body { width: 783px; height: 1200px; overflow: hidden; }
  body {
    position: relative;
    background: radial-gradient(ellipse at 50% 40%, #2a0d1c 0%, var(--page-bg) 55%, var(--page-bg-deep) 100%);
    color: var(--text);
    font-family: "Open Sans", Arial, sans-serif;
  }
  .abs { position: absolute; }

  /* Header */
  .site-header { position: absolute; left: 0; top: 0; width: 783px; height: 74px; background: var(--header-bg); }
  .phone-icon { left: 68px; top: 21px; width: 28px; height: 28px; border: 1.5px solid #fff; border-radius: 50%; display: flex; align-items: center; justify-content: center; }
  .phone-number { left: 105px; top: 26px; font-size: 14px; font-family: "Open Sans", Arial, sans-serif; }
  .brand-badge { background: var(--accent); border-radius: 3px; display: flex; flex-direction: column; align-items: center; justify-content: center; font-family: "Montserrat", Arial, sans-serif; font-weight: 700; color: #fff; line-height: 1.15; letter-spacing: 0.5px; }
  .brand-badge.header-brand { left: 343px; top: 13px; width: 97px; height: 48px; font-size: 11px; }
  .social-list { display: flex; gap: 8px; }
  .social-list .chip { width: 15px; height: 15px; border-radius: 2px; }
  .header-social { left: 629px; top: 28px; }
  .header-social .chip { background: #3b8fd6; }
  .header-social .chip.alt { background: var(--accent); }

  /* Navigation */
  .main-nav { position: absolute; left: 0; top: 74px; width: 783px; height: 36px; background: var(--nav-bg); }
  .nav-item { position: absolute; top: 0; height: 36px; line-height: 36px; font-size: 10.5px; transform: translateX(-50%); white-space: nowrap; font-family: "Open Sans", Arial, sans-serif; }
  .nav-item.active { width: 74px; text-align: center; background: #0e0d0e; border-top: 2px solid var(--accent); line-height: 32px; }

  /* Hero */
  .hero { left: 0; top: 110px; width: 783px; height: 322px; background: linear-gradient(100deg, #3a2418 0%, #5a3a22 30%, #2a1a22 55%, #3a2c5a 75%, #1b1426 100%); }
  .hero-shade { left: 0; top: 110px; width: 783px; height: 322px; background: linear-gradient(180deg, rgba(0,0,0,0) 40%, rgba(20,8,14,0.55) 100%); }
  .hero-title { left: 60px; top: 256px; font-family: "Montserrat", Arial, sans-serif; font-weight: 700; font-size: 40px; letter-spacing: 0.5px; }
  .hero-subtitle { left: 62px; top: 306px; font-size: 20px; }
  .hero-arrow { top: 396px; width: 16px; height: 16px; border-radius: 50%; background: rgba(0,0,0,0.55); display: flex; align-items: center; justify-content: center; }

  /* Events */
  .section-title { left: 0; top: 469px; width: 783px; text-align: center; font-family: "Montserrat", Arial, sans-serif; font-weight: 500; font-size: 19px; letter-spacing: 0.3px; }
  .event-card { width: 216px; height: 202px; overflow: hidden; }
  .event-photo { position: absolute; inset: 0; }
  .event-strip { position: absolute; left: 0; bottom: 0; width: 216px; height: 47px; background: var(--card-strip); }
  .event-date { position: absolute; left: 0; bottom: 0; width: 35px; height: 47px; background: #fff; color: #444; font-size: 7.5px; text-align: center; line-height: 1.5; padding-top: 7px; }
  .event-name { position: absolute; left: 42px; bottom: 26px; font-family: "Montserrat", Arial, sans-serif; font-weight: 500; font-size: 10px; }
  .event-blurb { position: absolute; left: 42px; bottom: 11px; font-size: 7.5px; color: #ddd; border-top: 1px solid #777; padding-top: 2px; }
  .book-button { position: absolute; left: 156px; bottom: 14px; width: 58px; height: 13px; border: 1px solid #ddd; border-radius: 7px; font-size: 6px; text-align: center; line-height: 11px; }

  .view-more { left: 344px; top: 962px; width: 94px; height: 24px; border: 1px solid #ddd; border-radius: 12px; text-align: center; line-height: 22px; font-size: 10.5px; }

  /* Footer */
  .site-footer { left: 0; top: 1010px; width: 783px; height: 190px; background: var(--footer-bg); }
  .brand-badge.footer-brand { left: 58px; top: 1066px; width: 97px; height: 48px; font-size: 11px; }
  .footer-heading { top: 1048px; font-size: 9.5px; }
  .footer-text { font-size: 7.5px; line-height: 14.5px; }
  .mail-input { left: 419px; top: 1099px; width: 95px; height: 19px; background: #fff; color: #888; font-size: 6.5px; line-height: 19px; padding-left: 5px; }
  .mail-submit { left: 514px; top: 1099px; width: 37px; height: 19px; background: #555; font-size: 6.5px; line-height: 19px; text-align: center; }
  .footer-social { left: 614px; top: 1078px; gap: 9px; }
  .footer-social .chip { width: 16px; height: 16px; background: #fff; border-radius: 3px; }
  .footer-rule { left: 50px; top: 1157px; width: 666px; height: 1px; background: var(--line); }
  .copyright { left: 0; top: 1173px; width: 783px; text-align: center; font-size: 7.5px; }
</style>
</head>
<body>

<header class="site-header">
  <div class="abs phone-icon">
    <svg width="13" height="13" viewBox="0 0 24 24"><path d="M6.6 10.8a15.1 15.1 0 0 0 6.6 6.6l2.2-2.2c.3-.3.7-.4 1-.2 1.1.4 2.3.6 3.6.6.6 0 1 .4 1 1V20c0 .6-.4 1-1 1A17 17 0 0 1 3 4c0-.6.4-1 1-1h3.5c.6 0 1 .4 1 1 0 1.3.2 2.5.6 3.6.1.3 0 .7-.2 1z" fill="#fff"/></svg>
  </div>
  <div class="abs phone-number">+852 5710 2284</div>
  <div class="abs brand-badge header-brand"><span>BROVLANE</span><span>PASS</span></div>
  <div class="abs social-list header-social">
    <span class="chip"></span><span class="chip"></span><span class="chip"></span><span class="chip alt"></span>
  </div>
</header>

<nav class="main-nav">
  <span class="nav-item active" style="left:94px">HOME</span>
  <span class="nav-item" style="left:181px">HOW TO ORDER</span>
  <span class="nav-item" style="left:277px">ABOUT US</span>
  <span class="nav-item" style="left:366px">CONTACT US</span>
  <span class="nav-item" style="left:450px">POLICIES</span>
  <span class="nav-item" style="left:524px">PRIVACY</span>
  <span class="nav-item" style="left:608px">CENTER SALE</span>
  <span class="nav-item" style="left:690px">ACCESS</span>
</nav>

<div class="abs hero" role="img" aria-label="Theatre hall with a seated audience facing a lit stage"></div>
<div class="abs hero-shade"></div>
<div class="abs hero-title">BROVLANE PASS</div>
<div class="abs hero-subtitle">quisquam est qui dolorem ipsum</div>
<div class="abs hero-arrow" style="left:686px"><svg width="6" height="8" viewBox="0 0 6 8"><path d="M4.5 1 1.5 4l3 3" stroke="#fff" stroke-width="1.2" fill="none"/></svg></div>
<div class="abs hero-arrow" style="left:708px"><svg width="6" height="8" viewBox="0 0 6 8"><path d="M1.5 1l3 3-3 3" stroke="#fff" stroke-width="1.2" fill="none"/></svg></div>

<h2 class="abs section-title">UPCOMING EVENTS</h2>

<article class="abs event-card" style="left:58px;top:513px">
  <div class="event-photo" role="img" aria-label="Band playing guitars on a concert stage" style="background:linear-gradient(135deg,#4a2a3a,#2a3050 60%,#1a1a2a)"></div>
  <div class="event-strip"></div>
  <div class="event-date">1<br>NOV<br>2017</div>
  <div class="event-name">NEQUE PORRO</div>
  <div class="event-blurb">Dolorem ipsum quia dolor</div>
  <div class="book-button">BOOK NOW</div>
</article>
<article class="abs event-card" style="left:284px;top:513px">
  <div class="event-photo" role="img" aria-label="Crowd with raised hands before bright stage lights" style="background:radial-gradient(ellipse at 50% 25%,#e09040,#8a4020 45%,#2a1008 100%)"></div>
  <div class="event-strip"></div>
  <div class="event-date">2<br>NOV<br>2017</div>
  <div class="event-name">NEQUE PORRO</div>
  <div class="event-blurb">Dolorem ipsum quia dolor</div>
  <div class="book-button">BOOK NOW</div>
</article>
<article class="abs event-card" style="left:509px;top:513px">
  <div class="event-photo" role="img" aria-label="Close view of a guitar being played under purple light" style="background:linear-gradient(135deg,#6a3050,#a04a70 45%,#3a2040)"></div>
  <div class="event-strip"></div>
  <div class="event-date">2<br>NOV<br>2017</div>
  <div class="event-name">NEQUE PORRO</div>
  <div class="event-blurb">Dolorem ipsum quia dolor</div>
  <div class="book-button">BOOK NOW</div>
</article>

<article class="abs event-card" style="left:58px;top:729px">
  <div class="event-photo" role="img" aria-label="Empty theatre with red curtain and rows of seats" style="background:linear-gradient(135deg,#7a2030,#3a5a8a 40%,#c8c8d8 70%,#6a2030)"></div>
  <div class="event-strip"></div>
  <div class="event-date">4<br>NOV<br>2017</div>
  <div class="event-name">NEQUE PORRO</div>
  <div class="event-blurb">Dolorem ipsum quia dolor</div>
  <div class="book-button">BOOK NOW</div>
</article>
<article class="abs event-card" style="left:284px;top:729px">
  <div class="event-photo" role="img" aria-label="Juggler in a colourful jester costume" style="background:linear-gradient(160deg,#5a2a4a,#8a3a8a 45%,#c8a030 70%,#3a1a30)"></div>
  <div class="event-strip"></div>
  <div class="event-date">5<br>NOV<br>2017</div>
  <div class="event-name">NEQUE PORRO</div>
  <div class="event-blurb">Dolorem ipsum quia dolor</div>
  <div class="book-button">BOOK NOW</div>
</article>
<article class="abs event-card" style="left:509px;top:729px">
  <div class="event-photo" role="img" aria-label="Rock band performing in blue stage haze" style="background:radial-gradient(ellipse at 60% 30%,#4a7a9a,#1a3a5a 50%,#0a1420 100%)"></div>
  <div class="event-strip"></div>
  <div class="event-date">6<br>NOV<br>2017</div>
  <div class="event-name">NEQUE PORRO</div>
  <div class="event-blurb">Dolorem ipsum quia dolor</div>
  <div class="book-button">BOOK NOW</div>
</article>

<div class="abs view-more">VIEW MORE</div>

<footer class="abs site-footer"></footer>
<div class="abs brand-badge footer-brand"><span>BROVLANE</span><span>PASS</span></div>

<div class="abs footer-heading" style="left:224px">CONTACT US</div>
<div class="abs footer-text" style="left:224px;top:1073px">
  Address : 1742 Corvane Ave,<br>
  Halden Park, FL, 33871<br>
  Phone : 508-417-2930<br>
  Email : hello@brovlanepass.net
</div>

<div class="abs footer-heading" style="left:419px">JOIN OUR MAILING LIST</div>
<div class="abs footer-text" style="left:419px;top:1071px;width:140px;font-size:7px;line-height:11px">Your about us information would fit here nicely.</div>
<div class="abs mail-input">Email address</div>
<div class="abs mail-submit">Submit</div>

<div class="abs footer-heading" style="left:614px">FOLLOW US OUT THERE</div>
<div class="abs social-list footer-social">
  <span class="chip"></span><span class="chip"></span><span class="chip"></span><span class="chip"></span>
</div>

<div class="abs footer-rule"></div>
<div class="abs copyright">Copyright © 2017. All Rights Reserved</div>

</body>
</html>
```